Custom hot rod builder needs a website for launch of new business where he will build luxury garages

We need a website that gives a WOW first impression for "Summit Carports". This is a new business so photos are renderings but we need it to really attract a particular audience. Our initial business is custom hot rods so now we are building garages for them. These will be like luxury "homes" for cars! I will attach our new logo. Website needs to feel powerful and prestigious.

Target Market(s)

middle aged men, car enthusiasts

Industry/Entity Type

automotive, construction

Coding

Coded - Design and coding required

Number of Pages Required

2 page

Font styles to use
Serif

Colors
0054AA
0677BA
7BADD7
CADEEF
E8F1F8

Requirements
Must have
• a WOW factor. luxury. contact form.
Nice to have
• ?

```html
<!DOCTYPE html>
<html lang="en">
<head>
<meta charset="utf-8">
<title>Summit Carports</title>
<link href="https://fonts.googleapis.com/css2?family=Michroma&family=Roboto:wght@400;500;700&display=swap" rel="stylesheet">
<style>
:root{
  --ink:#05060f;
  --blue:#29a9e1;
  --blue-deep:#1a8cc4;
  --white:#ffffff;
  --muted:#d8dde6;
  --photo-a:#4b5666;
  --photo-b:#2c333f;
}
*{margin:0;padding:0;box-sizing:border-box}
html,body{width:1200px;height:2971px;overflow:hidden;background:var(--ink)}
body{position:relative;font-family:'Roboto',sans-serif;color:var(--white)}
.abs{position:absolute}
.display{font-family:'Michroma',sans-serif;text-transform:uppercase;letter-spacing:1px}
.accent{color:var(--blue)}

/* header */
.site-header{left:0;top:0;width:1200px;height:83px;background:var(--ink);z-index:5}
.nav-link{position:absolute;top:31px;font-weight:700;font-size:15px;color:var(--white)}
.nav-link.active{color:var(--blue)}
.brand-badge{position:absolute;left:525px;top:-12px;width:150px;height:150px;border-radius:50%;background:var(--ink);display:flex;flex-direction:column;align-items:center;justify-content:center;padding-top:20px;color:var(--blue);font-weight:700;font-size:17px;line-height:1.15;text-align:center;text-transform:uppercase}
.social{position:absolute;top:23px;width:32px;height:32px;border-radius:50%;background:var(--blue)}

/* hero */
.hero-photo{left:0;top:83px;width:1200px;height:640px;background:linear-gradient(180deg,#56606e 0%,#6c7480 45%,#3f4a52 75%,#2f3a3a 100%)}
.hero-kicker{left:0;width:1200px;top:186px;text-align:center;font-size:20px;letter-spacing:3px}
.hero-title{left:0;width:1200px;top:228px;text-align:center;font-size:44px;letter-spacing:2px}
.hero-copy{left:130px;width:940px;top:292px;text-align:center;font-size:15px;line-height:22px}
.btn{position:absolute;background:var(--blue);color:var(--white);font-weight:700;font-size:15px;display:flex;align-items:center;justify-content:center;gap:10px;text-transform:uppercase;border-radius:2px}
.btn-dot{width:13px;height:13px;border-radius:50%;background:var(--white);position:relative}
.btn-dot::after{content:"";position:absolute;left:4px;top:3.5px;border-left:5px solid var(--blue);border-top:3px solid transparent;border-bottom:3px solid transparent}
.slider-dots{left:572px;top:454px;display:flex;gap:3px}
.slider-dots span{width:9px;height:9px;border-radius:50%;background:var(--white)}
.slider-dots span.off{background:transparent;border:1px solid var(--white)}

/* about */
.about-frame{left:108px;top:778px;width:434px;height:394px;border:10px solid var(--blue)}
.about-photo{left:127px;top:795px;width:426px;height:358px;background:linear-gradient(160deg,#5a4330 0%,#3b2c22 45%,#2a4a55 80%,#1e2a30 100%)}
.section-title{font-size:30px}
.rule{position:absolute;height:3px;width:37px;background:var(--blue)}
.about-copy{left:647px;top:900px;width:444px;font-size:15px;line-height:24px;text-align:justify}

/* services */
.services-photo{left:0;top:1256px;width:1200px;height:660px;background:linear-gradient(180deg,#4e5868 0%,#626b78 40%,#4a5158 75%,#3a4048 100%)}
.services-intro{left:111px;top:1445px;width:500px;font-size:15px;line-height:21px}
.service-icon{position:absolute;left:112px;width:88px;height:88px;border-radius:50%;background:var(--ink);display:flex;align-items:center;justify-content:center}
.service-icon .core{width:64px;height:64px;border-radius:50%;background:var(--blue);display:flex;align-items:center;justify-content:center}
.service-name{position:absolute;left:225px;font-weight:700;font-size:17px}
.service-text{position:absolute;left:225px;width:350px;font-size:13px;line-height:19px}
.car-art{left:651px;top:1602px;width:427px;height:231px;border-radius:90px 120px 40px 40px;background:linear-gradient(180deg,#3fb4ea 0%,#1d8fcf 60%,#2a3140 100%)}

/* why choose */
.why-title{left:0;width:1200px;top:1920px;text-align:center}
.why-copy{left:110px;width:980px;top:2000px;text-align:center;font-size:16px;line-height:26px}
.card{position:absolute;top:2144px;width:308px;height:273px;border:4px solid var(--blue);border-radius:14px;text-align:center}
.card-icon{position:absolute;top:-39px;left:102px;width:104px;height:86px;border-radius:10px;background:var(--blue);display:flex;align-items:center;justify-content:center}
.card-icon .inner{width:84px;height:68px;border:3px solid var(--ink);border-radius:8px;display:flex;align-items:center;justify-content:center}
.card h3{position:absolute;top:80px;left:0;width:100%;color:var(--blue);font-size:21px;font-weight:700}
.card .rule{left:117px;top:119px;height:2px;width:37px}
.card p{position:absolute;top:140px;left:22px;width:256px;font-size:14px;line-height:22px;text-align:justify;text-align-last:center}
.card .more{position:absolute;top:222px;left:0;width:100%;display:flex;justify-content:center;align-items:center;gap:8px;color:var(--blue);font-weight:700;font-size:13px}
.more .btn-dot{background:var(--blue);width:12px;height:12px}
.more .btn-dot::after{border-left-color:var(--ink);left:4px;top:3px}

/* footer */
.footer-brand{left:118px;top:2700px;width:180px;display:flex;flex-direction:column;align-items:center;gap:12px;color:var(--blue);font-weight:700;font-size:22px;text-transform:uppercase;text-align:center;line-height:1.2}
.footer-brand .mark{width:56px;height:56px;border-radius:50%;background:var(--blue)}
.footer-head{font-weight:700;font-size:14px}
.footer-line{position:absolute;height:1px;background:var(--muted)}
.footer-list{position:absolute;list-style:none;font-size:15px}
.footer-list li{height:34.3px;display:flex;align-items:flex-start;gap:14px}
.chev{color:var(--white);font-size:15px;width:10px}
.ficon{width:16px;display:flex;justify-content:center}
.newsletter-input{left:805px;top:2748px;width:284px;height:47px;background:var(--white);border-radius:3px;overflow:hidden}
.newsletter-input span{position:absolute;left:16px;top:15px;color:#777;font-size:14px}
.newsletter-input .send{position:absolute;right:0;top:0;width:42px;height:47px;background:var(--blue);display:flex;align-items:center;justify-content:center}
.ring{position:absolute;top:2823px;width:36px;height:36px;border:1px solid var(--white);border-radius:50%}
.bottom-bar{left:0;top:2919px;width:1200px;height:52px;background:var(--blue);text-align:center;font-size:15px;line-height:52px}
</style>
</head>
<body>

<!-- hero photo + curve -->
<div class="abs hero-photo" role="img" aria-label="Rendering of a modern luxury garage at dusk with palm trees and classic cars behind glass"></div>
<svg class="abs" style="left:0;top:520px" width="1200" height="250" viewBox="0 0 1200 250" aria-hidden="true">
  <path d="M0,195 Q600,-169 1200,195 L1200,250 L0,250 Z" fill="#29a9e1"/>
  <path d="M0,222 Q600,-146 1200,222 L1200,250 L0,250 Z" fill="#05060f"/>
</svg>

<header class="abs site-header">
  <span class="nav-link active" style="left:111px">Home</span>
  <span class="nav-link" style="left:180px">About</span>
  <span class="nav-link" style="left:248px">Our Services</span>
  <span class="nav-link" style="left:361px">Why Choose Us</span>
  <span class="nav-link" style="left:738px">Reviews</span>
  <span class="nav-link" style="left:821px">Contact Us</span>
  <span class="social" style="left:927px"></span>
  <span class="social" style="left:970px"></span>
  <span class="social" style="left:1012px"></span>
  <span class="social" style="left:1055px"></span>
</header>
<div class="brand-badge" style="z-index:6">Summit<br>Carports</div>

<div class="abs display hero-kicker">Welcome to</div>
<div class="abs display hero-title">Summit Carports</div>
<p class="abs hero-copy">At vero eos et accusamus et iusto odio dignissimos ducimus qui blanditiis praesentium voluptatum deleniti atque corrupti quos dolores et quas molestias excepturi sint occaecati cupiditate non provident, similique sunt in culpa qui officia deserunt</p>
<div class="btn" style="left:524px;top:348px;width:153px;height:45px">Get Started <span class="btn-dot"></span></div>
<div class="abs slider-dots"><span></span><span></span><span class="off"></span><span></span><span></span></div>

<!-- about -->
<svg class="abs" style="left:530px;top:760px" width="70" height="70" viewBox="0 0 70 70" aria-hidden="true">
  <g stroke="#29a9e1" stroke-width="4"><line x1="12" y1="12" x2="28" y2="2"/><line x1="12" y1="30" x2="42" y2="8"/><line x1="18" y1="44" x2="56" y2="18"/><line x1="32" y1="56" x2="62" y2="32"/></g>
</svg>
<svg class="abs" style="left:92px;top:1165px" width="100" height="65" viewBox="0 0 100 65" aria-hidden="true">
  <g stroke="#29a9e1" stroke-width="4"><line x1="6" y1="30" x2="30" y2="6"/><line x1="8" y1="42" x2="44" y2="6"/><line x1="14" y1="52" x2="58" y2="8"/><line x1="22" y1="60" x2="72" y2="8"/></g>
</svg>
<div class="abs about-frame"></div>
<div class="abs about-photo" role="img" aria-label="Interior rendering of the showroom garage with classic cars on display under track lighting"></div>

<h2 class="abs display section-title" style="left:647px;top:822px"><span class="accent">About</span> Us</h2>
<span class="rule" style="left:647px;top:874px"></span>
<p class="abs about-copy">At vero eos et accusamus et iusto odio dignissimos ducimus qui blanditiis praesentium voluptatum deleniti atque corrupti quos dolores et quas molestias excepturi sint occaecati cupiditate non provident, similique sunt in culpa qui officia deserunt mollitia animi, id est laborum et dolorum fuga. Et harum quidem rerum facilis est et expedita distinctio. Nam libero tempore, cum soluta nobis est eligendi optio cumque nihil impedit quo minus id quod maxime placeat facere possimus, omnis voluptas assumenda</p>
<div class="btn" style="left:647px;top:1113px;width:151px;height:44px">Learn More <span class="btn-dot"></span></div>

<!-- services -->
<div class="abs services-photo" role="img" aria-label="Exterior rendering of the luxury garage building at dusk"></div>
<svg class="abs" style="left:0;top:1255px" width="1200" height="90" viewBox="0 0 1200 90" aria-hidden="true">
  <path d="M0,0 Q600,164 1200,0 Z" fill="#05060f"/>
</svg>
<svg class="abs" style="left:0;top:1820px" width="1200" height="100" viewBox="0 0 1200 100" aria-hidden="true">
  <path d="M0,94 Q600,-67 1200,94 L1200,100 L0,100 Z" fill="#05060f"/>
</svg>

<h2 class="abs display section-title" style="left:111px;top:1366px"><span class="accent">Our</span> Services</h2>
<span class="rule" style="left:111px;top:1416px"></span>
<p class="abs services-intro">At vero eos et accusamus et iusto odio dignissimos ducimus qui blanditiis praesentium voluptatum deleniti atque corrupti quos dolores et quas</p>

<div class="service-icon" style="top:1501px"><div class="core">
  <svg width="38" height="30" viewBox="0 0 38 30" aria-hidden="true"><path d="M5,14 L9,5 H29 L33,14 H36 V24 H32 V28 H27 V24 H11 V28 H6 V24 H2 V14 Z" fill="#05060f"/><rect x="11" y="8" width="16" height="6" fill="#29a9e1"/><circle cx="9" cy="19" r="2.5" fill="#29a9e1"/><circle cx="29" cy="19" r="2.5" fill="#29a9e1"/></svg>
</div></div>
<div class="service-name" style="top:1511px">Lorem Ipsum Dolor</div>
<p class="service-text" style="top:1540px">Lorem ipsum dolor sit amet, consectetur adipiscing elit, sed do eiusmod tempor incididunt ut labore</p>

<div class="service-icon" style="top:1602px"><div class="core">
  <svg width="38" height="30" viewBox="0 0 38 30" aria-hidden="true"><path d="M5,14 L9,5 H29 L33,14 H36 V24 H32 V28 H27 V24 H11 V28 H6 V24 H2 V14 Z" fill="#05060f"/><rect x="11" y="8" width="16" height="6" fill="#29a9e1"/><circle cx="9" cy="19" r="2.5" fill="#29a9e1"/><circle cx="29" cy="19" r="2.5" fill="#29a9e1"/></svg>
</div></div>
<div class="service-name" style="top:1612px">Lorem Ipsum Dolor</div>
<p class="service-text" style="top:1641px">Lorem ipsum dolor sit amet, consectetur adipiscing elit, sed do eiusmod tempor incididunt ut labore</p>

<div class="service-icon" style="top:1702px"><div class="core">
  <svg width="38" height="30" viewBox="0 0 38 30" aria-hidden="true"><path d="M5,14 L9,5 H29 L33,14 H36 V24 H32 V28 H27 V24 H11 V28 H6 V24 H2 V14 Z" fill="#05060f"/><rect x="11" y="8" width="16" height="6" fill="#29a9e1"/><circle cx="9" cy="19" r="2.5" fill="#29a9e1"/><circle cx="29" cy="19" r="2.5" fill="#29a9e1"/></svg>
</div></div>
<div class="service-name" style="top:1712px">Lorem Ipsum Dolor</div>
<p class="service-text" style="top:1741px">Lorem ipsum dolor sit amet, consectetur adipiscing elit, sed do eiusmod tempor incididunt ut labore</p>

<div class="abs car-art" role="img" aria-label="Illustration of a blue classic hot rod coupe"></div>

<!-- why choose us -->
<h2 class="abs display section-title why-title"><span class="accent">Why Choose</span> Us</h2>
<span class="rule" style="left:581px;top:1970px"></span>
<p class="abs why-copy">Sed ut perspiciatis unde omnis iste natus error sit voluptatem accusantium doloremque laudantium, totam rem aperiam, eaque ipsa quae ab illo inventore veritatis et quasi architecto beatae vitae dicta sunt explicabo.</p>

<div class="card" style="left:108px">
  <div class="card-icon"><div class="inner"><svg width="40" height="36" viewBox="0 0 40 36" aria-hidden="true"><path d="M2,14 L20,3 L38,14 V34 H32 V16 H8 V34 H2 Z" fill="#05060f"/><rect x="11" y="22" width="18" height="8" rx="2" fill="#05060f"/></svg></div></div>
  <h3>Lorem Ipsum Dolor</h3><span class="rule"></span>
  <p>Lorem ipsum dolor sit amet, consectetur adipiscing elit, sed do eiusmod tempor incididunt ut labore et dolore</p>
  <div class="more">LEARN MORE <span class="btn-dot"></span></div>
</div>
<div class="card" style="left:446px">
  <div class="card-icon"><div class="inner"><svg width="40" height="36" viewBox="0 0 40 36" aria-hidden="true"><rect x="4" y="10" width="32" height="24" fill="#05060f"/><rect x="9" y="15" width="22" height="4" fill="#29a9e1"/><rect x="9" y="22" width="22" height="4" fill="#29a9e1"/><rect x="10" y="2" width="20" height="5" fill="#05060f"/></svg></div></div>
  <h3>Lorem Ipsum Dolor</h3><span class="rule"></span>
  <p>Lorem ipsum dolor sit amet, consectetur adipiscing elit, sed do eiusmod tempor incididunt ut labore et dolore</p>
  <div class="more">LEARN MORE <span class="btn-dot"></span></div>
</div>
<div class="card" style="left:784px">
  <div class="card-icon"><div class="inner"><svg width="40" height="36" viewBox="0 0 40 36" aria-hidden="true"><path d="M4,12 L20,2 L36,12" stroke="#05060f" stroke-width="3" fill="none"/><path d="M9,24 L12,16 H28 L31,24 H33 V32 H7 V24 Z" fill="#05060f"/></svg></div></div>
  <h3>Lorem Ipsum Dolor</h3><span class="rule"></span>
  <p>Lorem ipsum dolor sit amet, consectetur adipiscing elit, sed do eiusmod tempor incididunt ut labore et dolore</p>
  <div class="more">LEARN MORE <span class="btn-dot"></span></div>
</div>

<!-- footer arc -->
<svg class="abs" style="left:0;top:2425px" width="1200" height="210" viewBox="0 0 1200 210" aria-hidden="true">
  <path d="M0,0 Q600,364 1200,0 L1200,24 Q600,384 0,24 Z" fill="#29a9e1"/>
</svg>

<!-- footer -->
<div class="abs footer-brand"><span class="mark"></span>Summit<br>Carports</div>

<div class="abs footer-head" style="left:356px;top:2658px">LINKS</div>
<span class="footer-line" style="left:356px;top:2685px;width:359px"></span>
<ul class="footer-list" style="left:356px;top:2708px">
  <li><span class="chev">»</span><span style="margin-left:5px">Home</span></li>
  <li><span class="chev">»</span><span style="margin-left:5px">About us</span></li>
  <li><span class="chev">»</span><span style="margin-left:5px">Our Services</span></li>
  <li><span class="chev">»</span><span style="margin-left:5px">Why Choose Us</span></li>
  <li><span class="chev">»</span><span style="margin-left:5px">Tutorials</span></li>
</ul>
<ul class="footer-list" style="left:516px;top:2708px">
  <li><span class="ficon"><svg width="14" height="11" viewBox="0 0 14 11" aria-hidden="true"><rect width="14" height="11" rx="1" fill="#fff"/><path d="M0,1 L7,6 L14,1" stroke="#05060f" stroke-width="1.5" fill="none"/></svg></span>info@summitcarports.com</li>
  <li><span class="ficon"><svg width="13" height="13" viewBox="0 0 13 13" aria-hidden="true"><path d="M2,1 L5,1 L6,4 L4,5.5 Q5.5,8 7.5,9 L9,7 L12,8 L12,11 Q6,12 2,7 Q0.5,4 2,1 Z" fill="#fff"/></svg></span>+ 1 555 010 2040</li>
  <li><span class="ficon"><svg width="11" height="15" viewBox="0 0 11 15" aria-hidden="true"><path d="M5.5,0 A5.5,5.5 0 0 1 11,5.5 Q11,9 5.5,15 Q0,9 0,5.5 A5.5,5.5 0 0 1 5.5,0 Z" fill="#fff"/><circle cx="5.5" cy="5.5" r="2" fill="#05060f"/></svg></span>145 , Lorem Ipsum Dolor</li>
  <li><span class="ficon"></span>United States</li>
  <li><span class="ficon"><svg width="15" height="13" viewBox="0 0 15 13" aria-hidden="true"><path d="M0,2 L5,0 L10,2 L15,0 V11 L10,13 L5,11 L0,13 Z" fill="#fff"/><path d="M5,0 V11 M10,2 V13" stroke="#05060f" stroke-width="1"/></svg></span>View Other Location</li>
</ul>

<div class="abs footer-head" style="left:803px;top:2658px">NEWSLETTER</div>
<span class="footer-line" style="left:803px;top:2685px;width:280px"></span>
<div class="abs" style="left:803px;top:2711px;font-size:15px">Send us a newsletter to get update</div>
<div class="abs newsletter-input">
  <span>Email Address</span>
  <div class="send"><svg width="16" height="16" viewBox="0 0 16 16" aria-hidden="true"><path d="M1,8 L15,1 L11,15 L8,9 Z" fill="none" stroke="#fff" stroke-width="1.5" stroke-linejoin="round"/></svg></div>
</div>
<span class="ring" style="left:804px"></span>
<span class="ring" style="left:847px"></span>
<span class="ring" style="left:890px"></span>
<span class="ring" style="left:934px"></span>

<div class="abs bottom-bar">© 2022 Summit Carports. All Rights Reserved</div>

</body>
</html>
```